Coconut Water Packaging Appealing to Hispanic Consumers

This is a design for an aluminum can containing coconut water with pulp

Brand Name: Brisamar Coconut Water
Details:16.5fl oz (490ml)
Image: Animated man standing on a beach drinking out of a green coconut with a straw wearing sunglasses
Blurbs: "with pulp" "agua de coco con pulpa"
Background: Beach setting, sand, palm trees and ocean
Die cut attached

Target Market(s)

First and second generation Hispanic, Spanish speaking and price conscious consumers

Requirements
Must have
• Brand Name: Brisamar Coconut Water
Nice to have
• beach setting, refreshing feel

```html
<!DOCTYPE html>
<html lang="en">
<head>
<meta charset="utf-8">
<title>Brisamar Coconut Water – Can Label</title>
<link href="https://fonts.googleapis.com/css2?family=Arimo:ital,wght@0,400;0,700;1,400&family=Bangers&family=Libre+Franklin:wght@900&family=Roboto+Condensed:wght@300&display=swap" rel="stylesheet">
<style>
  :root {
    --page-bg: #e6e6e6;
    --sky-top: #2f8fd0;
    --sky-low: #a8daf0;
    --cloud: #e9f5fb;
    --sea-deep: #1479c4;
    --sea-shallow: #5cc9d6;
    --foam: #f4f8f6;
    --sand-light: #f6e3b4;
    --sand-warm: #f2c98d;
    --brand-red: #d5121b;
    --banner-yellow: #f3e21c;
    --ink: #111111;
    --panel: #ffffff;
    --figure-skin: #e47f3c;
    --figure-shirt: #4e5140;
  }
  * { box-sizing: border-box; margin: 0; padding: 0; }
  html, body { width: 1200px; height: 960px; overflow: hidden; }
  body { background: var(--page-bg); font-family: "Arimo", Arial, sans-serif; color: var(--ink); position: relative; }

  .label { position: absolute; left: 0; top: 16px; width: 1200px; height: 927px; overflow: hidden; }
  .beach-scene { position: absolute; inset: 0; width: 100%; height: 100%; }

  .beach-figure {
    position: absolute; left: 600px; top: 300px; width: 350px; height: 640px;
    background: linear-gradient(180deg,
      rgba(228,127,60,0) 0%,
      var(--figure-skin) 10%,
      var(--figure-skin) 34%,
      var(--figure-shirt) 48%,
      var(--figure-shirt) 100%);
    border-radius: 50% 50% 0 0 / 22% 22% 0 0;
    opacity: 0.85;
  }

  .brand-name {
    position: absolute; left: 440px; top: 140px; width: 440px;
    text-align: center; color: var(--brand-red);
    font-family: "Bangers", "Arimo", sans-serif; font-weight: 400; text-transform: uppercase;
    line-height: 1; letter-spacing: 2px;
  }
  .brand-name .brand-main { display: block; font-size: 112px; }
  .brand-name .brand-sub { display: block; font-size: 66px; margin-top: -4px; }

  .pulp-banner { position: absolute; left: 446px; top: 448px; width: 280px; height: 118px; }
  .pulp-banner-text {
    position: absolute; left: 470px; top: 478px; transform: rotate(11deg);
    font-family: "Bangers", "Arimo", sans-serif; font-size: 38px; color: #ffffff; letter-spacing: 1px;
  }

  .nutrition-facts {
    position: absolute; left: 29px; top: 67px; width: 268px;
    background: var(--panel); border: 1.5px solid var(--ink); padding: 3px 5px 4px;
    font-size: 12.5px; line-height: 1.15;
  }
  .nf-title { font-family: "Libre Franklin", "Arimo", sans-serif; font-weight: 900; font-size: 29px; line-height: 1.05; letter-spacing: -0.5px; }
  .nf-serving { font-size: 12px; }
  .nf-bar-thick { height: 10px; background: var(--ink); margin: 3px 0 2px; }
  .nf-bar-mid { height: 5px; background: var(--ink); margin: 1px 0 2px; }
  .nf-small-bold { font-size: 9.5px; font-weight: 700; padding: 2px 0; }
  .nf-right { text-align: right; }
  .nf-row { display: flex; justify-content: space-between; border-top: 1px solid #777; padding: 2px 0 1px; min-height: 18.4px; }
  .nf-row.first { border-top: 0; }
  .nf-row.indent { padding-left: 16px; }
  .nf-row b { font-weight: 700; }
  .nf-footnote { font-size: 9px; line-height: 1.2; padding: 5px 0 3px; border-top: 1px solid #777; }
  .nf-footnote span { display: block; padding-left: 6px; }
  .nf-limits { width: 100%; border-collapse: collapse; font-size: 8.6px; line-height: 1.25; border-top: 1px solid #777; }
  .nf-limits td { padding: 0; }
  .nf-limits .sub { padding-left: 14px; }

  .ingredients { position: absolute; left: 28px; top: 638px; width: 284px; font-size: 17.8px; line-height: 22px; }
  .ingredients b { font-weight: 700; }
  .side-blurb { position: absolute; left: 988px; top: 628px; width: 172px; font-size: 17.8px; line-height: 22px; }

  .volume {
    position: absolute; left: 533px; top: 838px; width: 200px; text-align: center;
    font-family: "Roboto Condensed", "Arimo", sans-serif; font-weight: 300; font-size: 24px; color: #222;
    background: radial-gradient(ellipse at center, rgba(255,255,255,0.95) 35%, rgba(255,255,255,0) 70%);
    padding: 8px 0;
  }
</style>
</head>
<body>
  <main class="label">
    <svg class="beach-scene" viewBox="0 0 1200 927" preserveAspectRatio="none" role="img" aria-label="Illustrated beach scene with sky, clouds, ocean, sand, parasol, deck chairs and palm leaves">
      <defs>
        <linearGradient id="sky" x1="0" y1="0" x2="0" y2="1">
          <stop offset="0" stop-color="var(--sky-top)"/>
          <stop offset="1" stop-color="var(--sky-low)"/>
        </linearGradient>
        <linearGradient id="clouds" x1="0" y1="0" x2="0" y2="1">
          <stop offset="0" stop-color="var(--cloud)" stop-opacity="0"/>
          <stop offset="1" stop-color="var(--cloud)" stop-opacity="0.8"/>
        </linearGradient>
        <linearGradient id="sea" x1="0" y1="0" x2="0" y2="1">
          <stop offset="0" stop-color="var(--sea-deep)"/>
          <stop offset="1" stop-color="var(--sea-shallow)"/>
        </linearGradient>
        <linearGradient id="sand" x1="0" y1="0" x2="0" y2="1">
          <stop offset="0" stop-color="var(--sand-light)"/>
          <stop offset="1" stop-color="var(--sand-warm)"/>
        </linearGradient>
      </defs>
      <rect x="0" y="0" width="1200" height="410" fill="url(#sky)"/>
      <rect x="0" y="250" width="1200" height="160" fill="url(#clouds)"/>
      <rect x="0" y="405" width="1200" height="150" fill="url(#sea)"/>
      <rect x="0" y="545" width="1200" height="25" fill="var(--foam)"/>
      <rect x="0" y="565" width="1200" height="362" fill="url(#sand)"/>
    </svg>

    <div class="beach-figure" role="img" aria-label="Cartoon man in a tank top and glasses holding a green coconut with a straw"></div>

    <h1 class="brand-name">
      <span class="brand-main">Brisamar</span>
      <span class="brand-sub">Coconut Water</span>
    </h1>

    <svg class="pulp-banner" viewBox="0 0 280 118" aria-hidden="true">
      <polygon points="14,8 280,66 250,118 0,92" fill="var(--banner-yellow)"/>
      <polygon points="10,0 270,60 244,110 2,84" fill="var(--brand-red)"/>
    </svg>
    <div class="pulp-banner-text">With Pulp</div>

    <section class="nutrition-facts" aria-label="Nutrition Facts">
      <div class="nf-title">Nutrition Facts</div>
      <div class="nf-serving">Serving Size 2/3 cup (55g)<br>Servings Per Container About 8</div>
      <div class="nf-bar-thick"></div>
      <div class="nf-small-bold">Amount Per Serving</div>
      <div class="nf-row first"><span><b>Calories</b> 230</span><span>Calories from Fat 40</span></div>
      <div class="nf-bar-mid"></div>
      <div class="nf-small-bold nf-right">% Daily Value*</div>
      <div class="nf-row"><span><b>Total Fat</b> 8g</span><b>12%</b></div>
      <div class="nf-row indent"><span>Saturated Fat 1g</span><b>5%</b></div>
      <div class="nf-row indent"><span><i>Trans</i> Fat 0g</span><span></span></div>
      <div class="nf-row"><span><b>Cholesterol</b> 0mg</span><b>0%</b></div>
      <div class="nf-row"><span><b>Sodium</b> 160mg</span><b>7%</b></div>
      <div class="nf-row"><span><b>Total Carbohydrate</b> 37g</span><b>12%</b></div>
      <div class="nf-row indent"><span>Dietary Fiber 4g</span><b>16%</b></div>
      <div class="nf-row indent"><span>Sugars 1g</span><span></span></div>
      <div class="nf-row"><span><b>Protein</b> 3g</span><span></span></div>
      <div class="nf-bar-thick"></div>
      <div class="nf-row first"><span>Vitamin A</span><span>10%</span></div>
      <div class="nf-row"><span>Vitamin C</span><span>8%</span></div>
      <div class="nf-row"><span>Calcium</span><span>20%</span></div>
      <div class="nf-row"><span>Iron</span><span>45%</span></div>
      <div class="nf-footnote">* Percent Daily Values are based on a 2,000 calorie diet.<span>Your daily value may be higher or lower depending on your calorie needs.</span></div>
      <table class="nf-limits">
        <tr><td></td><td>Calories:</td><td>2,000</td><td>2,500</td></tr>
        <tr><td>Total Fat</td><td>Less than</td><td>65g</td><td>80g</td></tr>
        <tr><td class="sub">Sat Fat</td><td>Less than</td><td>20g</td><td>25g</td></tr>
        <tr><td>Cholesterol</td><td>Less than</td><td>300mg</td><td>300mg</td></tr>
        <tr><td>Sodium</td><td>Less than</td><td>2,400mg</td><td>2,400mg</td></tr>
        <tr><td>Total Carbohydrate</td><td></td><td>300g</td><td>375g</td></tr>
        <tr><td class="sub">Dietary Fiber</td><td></td><td>25g</td><td>30g</td></tr>
      </table>
    </section>

    <p class="ingredients"><b>Ingredients:</b> Lorem ipsum dolor sit amet, consectetuer adipiscing elit, sed diam nonummy nibh euismod tincidunt ut laoreet dolore magna aliquam erat volutpat. Ut wisi enim ad minim veniam, quis nostrud exerci tation</p>

    <p class="side-blurb">Saim dolor sit amet, consectetuer adipiscing elit, sed diam nonummy nibh euismod tincidunt ut laoreet dolore magna aliquam erat volutpat. Ut wisi enim ad minim veniam, quis nostrud exerci tation</p>

    <div class="volume">16.5fl oz (490ml)</div>
  </main>
</body>
</html>
```